Verodex business card

Business card for sustainable investment company called "Verodex". Verodex is an exchange platform selling carbon credits between buyers and sellers. Carbon Credits are an environmental commodity for reducing global carbon emissions.

the card should obviously have our logo and the theme should be sustainability/environment mixed with a trading platform.

Contact Information for Business Card

Logo, Name, Title, Phone, Email

Colors
0054AA
0677BA
7BADD7
CADEEF
E8F1F8
0094D4
00A9DD
6FCCEA
C7EBF8
E9F6FB
00AB8E
00BBA5
67D7C9
C6EFE9
E9F9F6
59FF00
82FF00
B8FF75
E3FFCB
F4FFEA

```html
<!DOCTYPE html>
<html lang="en">
<head>
<meta charset="utf-8">
<title>Verodex Business Card</title>
<link rel="stylesheet" href="https://fonts.googleapis.com/css2?family=Poppins:wght@400;600&display=swap">
<style>
  :root {
    --page-bg: #ececec;
    --card-white: #ffffff;
    --navy: #22344f;
    --ink: #1c2433;
    --aqua: #36e8ee;
    --sky: #27a6ea;
    --accent-blue: #2a86ee;
  }
  * { margin: 0; padding: 0; box-sizing: border-box; }
  html, body {
    width: 1093px;
    height: 1200px;
    overflow: hidden;
    background: var(--page-bg);
    font-family: "Poppins", sans-serif;
  }
  .canvas { position: relative; width: 1093px; height: 1200px; }
  .card {
    position: absolute;
    left: 264px;
    width: 579px;
    height: 357px;
    overflow: hidden;
  }
  .card-front { top: 226px; background: var(--card-white); }
  .card-back { top: 620px; background: var(--navy); }

  .accent-band {
    position: absolute;
    top: 0;
    right: 0;
    width: 300px;
    height: 100%;
  }

  .holder { position: absolute; left: 27px; top: 80px; color: var(--navy); }
  .holder-name { font-weight: 600; font-size: 23px; letter-spacing: 0.3px; line-height: 1; }
  .holder-title { font-weight: 400; font-size: 16.5px; line-height: 1.2; color: var(--ink); }

  .contact-list { position: absolute; left: 27px; top: 216px; list-style: none; }
  .contact-item {
    display: flex;
    align-items: center;
    height: 21px;
    font-size: 17px;
    color: var(--ink);
  }
  .contact-icon { width: 16px; height: 16px; margin-right: 7px; flex: none; }

  .brand {
    position: absolute;
    left: 0; right: 0; top: 0; bottom: 0;
    display: flex;
    align-items: center;
    justify-content: center;
    gap: 18px;
  }
  .brand-square { width: 46px; height: 46px; background: var(--accent-blue); }
  .brand-name {
    font-weight: 600;
    font-size: 46px;
    color: #ffffff;
    letter-spacing: 0.5px;
    line-height: 1;
  }
</style>
</head>
<body>
<main class="canvas">
  <section class="card card-front">
    <svg class="accent-band" viewBox="0 0 300 357" preserveAspectRatio="none" role="img" aria-label="Brand gradient panel">
      <defs>
        <linearGradient id="bandGradient" x1="0" y1="0" x2="1" y2="0">
          <stop offset="0" stop-color="#36e8ee"/>
          <stop offset="1" stop-color="#27a6ea"/>
        </linearGradient>
      </defs>
      <rect x="0" y="0" width="300" height="357" fill="url(#bandGradient)"/>
    </svg>

    <div class="holder">
      <h1 class="holder-name">MARCUS HALE</h1>
      <p class="holder-title">Managing Director</p>
    </div>

    <ul class="contact-list">
      <li class="contact-item">
        <svg class="contact-icon" viewBox="0 0 24 24" aria-hidden="true"><path fill="#22344f" d="M6.6 10.8a15.1 15.1 0 0 0 6.6 6.6l2.2-2.2c.3-.3.7-.4 1-.2 1.1.4 2.3.6 3.6.6.6 0 1 .4 1 1V20c0 .6-.4 1-1 1C10.6 21 3 13.4 3 4c0-.6.4-1 1-1h3.5c.6 0 1 .4 1 1 0 1.3.2 2.5.6 3.6.1.3 0 .7-.2 1z"/></svg>
        044-987 650 312
      </li>
      <li class="contact-item">
        <svg class="contact-icon" viewBox="0 0 24 24" aria-hidden="true"><path fill="#22344f" d="M2 5h20v14H2z"/><path fill="none" stroke="#fff" stroke-width="1.6" d="M2.5 5.5 12 13l9.5-7.5"/></svg>
        hello@verodex.com
      </li>
      <li class="contact-item">
        <svg class="contact-icon" viewBox="0 0 24 24" aria-hidden="true"><g fill="none" stroke="#22344f" stroke-width="2"><circle cx="12" cy="12" r="9.5"/><ellipse cx="12" cy="12" rx="4" ry="9.5"/><path d="M2.5 12h19M4 7h16M4 17h16"/></g></svg>
        www.verodex.com
      </li>
    </ul>
  </section>

  <section class="card card-back">
    <div class="brand">
      <span class="brand-square" aria-hidden="true"></span>
      <span class="brand-name">VERODEX</span>
    </div>
  </section>
</main>
</body>
</html>
```